Luxury WordPress Website for CORALBASINS

I need a professional WordPress website for Coral Basins. The site should be modern, visually appealing, and user-friendly, reflecting the brand’s luxury and premium identity. It must include a homepage, product/service pages, contact form, and be responsive on both desktop and mobile devices. The design should allow for easy updates and integration of future content, while maintaining a polished and professional look.

Target Market(s)

swimmingpool & spa

Industry/Entity Type

Swimmingpool

Coding

Coded - Design and coding required

Font styles to use
Other font styles liked:
• HaboroSoft

Requirements
Must have
• Exclusive appearance
Nice to have
• • A logo that subtly incorporates water or pool elements. • A color palette that reflects luxury, elegance, and relaxation. • Clean and modern typography that is easy to read across all media. • Iconography or design elements that convey premium quality. • A versatile design that can be adapted for social media, merchandise, and promotional materials. • Optional: A tagline that emphasizes luxury and high-end pool experiences.

```html
<!DOCTYPE html>
<html lang="en">
<head>
<meta charset="utf-8">
<title>Coral Basins — Luxury Pool Design</title>
<link href="https://fonts.googleapis.com/css2?family=Nunito+Sans:wght@300;400;600;700&display=swap" rel="stylesheet">
<style>
:root{
  --blue:#0b4fa6;
  --blue-deep:#083e86;
  --navy:#0b1e36;
  --ink:#1a1f2b;
  --muted:#3a4150;
  --white:#ffffff;
  --band:#4d4d4f;
  --line:#c9d6ea;
  --star:#0b4fa6;
}
*{margin:0;padding:0;box-sizing:border-box}
html,body{width:1200px;height:3331px;overflow:hidden}
body{font-family:"Nunito Sans",sans-serif;color:var(--ink);background:var(--white);position:relative}
.abs{position:absolute}
a{color:inherit;text-decoration:none}

/* Hero */
.hero{position:absolute;left:0;top:0;width:1200px;height:612px;
  background:linear-gradient(180deg,#a9c9d6 0%,#8fb0c0 30%,#6b8e9c 52%,#4d7283 68%,#2e5e74 82%,#5d7d8c 100%)}
.hero-scene{position:absolute;inset:0}
.brand{position:absolute;left:90px;top:64px;display:flex;align-items:center;gap:12px;color:var(--blue);font-size:31px;font-weight:400}
.brand-dot{width:44px;height:44px;border-radius:50%;background:#8fa3b8}
.nav{position:absolute;left:424px;top:80px;display:flex;gap:30px;font-size:14px;color:var(--ink)}
.nav .active{color:var(--blue);border-bottom:1px solid var(--blue);padding-bottom:6px}
.nav-search{position:absolute;left:878px;top:80px}
.btn-touch{position:absolute;left:920px;top:67px;width:168px;height:44px;background:#fff;border-radius:3px;display:flex;align-items:center;justify-content:space-between;padding:0 20px;font-size:14px;box-shadow:0 2px 6px rgba(0,0,0,.12)}
.hero-title{position:absolute;left:111px;top:228px;font-size:45px;line-height:52px;font-weight:400;color:#fff}
.hero-title span{color:var(--blue)}
.hero-sub{position:absolute;left:111px;top:354px;width:470px;font-size:14.5px;line-height:26px;color:#fff}
.btn-primary{background:var(--blue);color:#fff;border-radius:3px;display:flex;align-items:center;justify-content:space-between;padding:0 20px;font-size:14.5px;font-weight:600}
.btn-schedule{position:absolute;left:111px;top:454px;width:257px;height:41px}
.play{position:absolute;left:385px;top:454px;width:42px;height:42px;border-radius:50%;background:#fff;display:flex;align-items:center;justify-content:center}
.play-label{position:absolute;left:440px;top:465px;font-size:14.5px;color:var(--ink)}

/* Partner band */
.partners{position:absolute;left:0;top:612px;width:1200px;height:103px;background:var(--band)}
.partner{position:absolute;top:39px;display:flex;align-items:center;gap:8px;color:#fff;font-size:20px;font-weight:400}
.partner i{width:22px;height:22px;border-radius:50%;background:#8fd0e8;display:block}

/* Section headings */
.sec-title{position:absolute;left:111px;font-size:40px;line-height:48px;font-weight:400;color:var(--ink)}
.sec-title span{color:var(--blue);display:block}
.sec-lead{position:absolute;left:515px;width:545px;font-size:14px;line-height:26px;color:var(--ink)}

/* Services */
.card-feature{position:absolute;left:59px;top:950px;width:404px;height:440px;border:1.5px solid #2f7bd6;border-radius:4px;overflow:hidden;
  background:linear-gradient(180deg,#f6f7f8 0%,#eef1f3 45%,#d7eaf3 75%,#b9d8c9 100%)}
.card-photo{position:absolute;right:0;top:0;width:162px;height:165px;background:linear-gradient(180deg,#9cc9e8 0%,#b9a58d 45%,#2ab3e6 70%,#5ea04a 100%)}
.svc-icon{position:absolute}
.svc-title{position:absolute;font-size:25px;line-height:31px;font-weight:400;color:var(--ink)}
.svc-title.hl{color:var(--blue)}
.svc-text{position:absolute;width:300px;font-size:14px;line-height:26px;color:var(--ink)}
.btn-service{position:absolute;left:103px;top:1292px;width:281px;height:41px}
.btn-outline{position:absolute;width:131px;height:42px;border:1.5px solid var(--blue);border-radius:3px;color:var(--blue);font-size:14px;display:flex;align-items:center;justify-content:center;background:#fff}
.slider{position:absolute;left:500px;top:1420px;width:199px;height:42px;border:1.5px solid var(--blue);border-radius:3px}
.slider-next{position:absolute;left:604px;top:1406px;width:66px;height:66px;border-radius:50%;background:#e6eef8;border:1px solid var(--line);display:flex;align-items:center;justify-content:center}

/* About */
.about{position:absolute;left:0;top:1564px;width:1200px;height:630px;background:linear-gradient(120deg,#0e3f7a 0%,#0f5596 45%,#0b5aa8 75%,#0a4f9e 100%)}
.about-back{position:absolute;left:123px;top:1663px;width:411px;height:438px;background:var(--blue);border-radius:6px}
.about-photo{position:absolute;left:114px;top:1681px;width:403px;height:438px;border-radius:6px;background:linear-gradient(180deg,#5b6f91 0%,#8b7fa0 30%,#b47a52 55%,#1c8ff0 78%,#3ab8ff 100%)}
.about-title{position:absolute;left:623px;top:1676px;font-size:40px;line-height:46px;color:#fff;font-weight:400}
.about-text{position:absolute;left:623px;top:1788px;width:470px;font-size:14px;line-height:26px;color:#fff}
.about-list{position:absolute;left:623px;top:1884px;list-style:none;color:#fff;font-size:14px;line-height:27.5px}
.about-list li{padding-left:20px;position:relative}
.about-list li::before{content:"";position:absolute;left:2px;top:11px;width:6px;height:6px;border-radius:50%;background:#fff}
.btn-white{position:absolute;left:623px;top:2031px;width:167px;height:42px;background:#fff;border-radius:3px;color:var(--blue);font-size:14px;display:flex;align-items:center;justify-content:space-between;padding:0 22px}

/* Testimonials */
.review{position:absolute;top:2463px;width:294px;height:410px;background:#fff;box-shadow:0 6px 24px rgba(20,40,80,.08)}
.quote{position:absolute;left:32px;top:36px;font-size:96px;line-height:1;font-weight:700;color:var(--navy);font-family:Georgia,serif}
.stars{position:absolute;left:125px;top:52px;display:flex;gap:4px}
.avatar{position:absolute;left:25px;top:118px;width:70px;height:70px;border-radius:50%;background:var(--navy);color:#fff;font-size:34px;display:flex;align-items:center;justify-content:center;font-weight:300}
.rev-name{position:absolute;left:114px;top:140px;font-size:20px;color:var(--muted)}
.rev-text{position:absolute;left:27px;top:218px;width:250px;font-size:14px;line-height:26px;color:var(--muted)}

/* Footer */
.footer{position:absolute;left:0;top:2978px;width:1200px;height:353px;background:var(--blue)}
.foot-brand{position:absolute;left:0;top:68px;width:1200px;display:flex;justify-content:center;align-items:center;gap:16px;color:#fff;font-size:44px}
.foot-brand i{width:60px;height:60px;border-radius:50%;background:#9fb3c9;display:block}
.foot-nav{position:absolute;left:0;top:190px;width:1200px;display:flex;justify-content:center;gap:40px;color:#fff;font-size:17px}
.socials{position:absolute;left:0;top:249px;width:1200px;display:flex;justify-content:center;gap:16px}
.socials i{width:21px;height:21px;border-radius:50%;background:#fff;display:block}
.copy{position:absolute;left:0;top:302px;width:1200px;text-align:center;color:#fff;font-size:11px}
</style>
</head>
<body>

<header class="hero">
  <div class="hero-scene" role="img" aria-label="Infinity pool overlooking misty mountain valley with thatched pavilions and tropical trees"></div>
  <div class="brand"><span class="brand-dot"></span>Coral Basins</div>
  <nav class="nav">
    <a class="active">Home</a><a>Services</a><a>About Us</a><a>Testimonials</a><a>Contact</a>
  </nav>
  <svg class="nav-search" width="16" height="16" viewBox="0 0 16 16"><circle cx="6.5" cy="6.5" r="4.5" fill="none" stroke="#0b4fa6" stroke-width="2"/><line x1="10" y1="10" x2="14" y2="14" stroke="#0b4fa6" stroke-width="2"/></svg>
  <a class="btn-touch">Get in Touch
    <svg width="18" height="18" viewBox="0 0 24 24"><path d="M6.6 10.8a15 15 0 0 0 6.6 6.6l2.2-2.2a1 1 0 0 1 1-.25 11 11 0 0 0 3.6.6 1 1 0 0 1 1 1V20a1 1 0 0 1-1 1A17 17 0 0 1 3 4a1 1 0 0 1 1-1h3.5a1 1 0 0 1 1 1 11 11 0 0 0 .6 3.6 1 1 0 0 1-.25 1z" fill="none" stroke="#0b4fa6" stroke-width="1.8"/></svg>
  </a>
  <h1 class="hero-title">Experience the Pinnacle of<br><span>Luxury Pool Design</span></h1>
  <p class="hero-sub">Redefining elegance and performance through innovative design, premium craftsmanship, and timeless appeal.</p>
  <a class="btn-primary btn-schedule">Schedule an Appointment
    <svg width="18" height="18" viewBox="0 0 24 24"><path d="M6.6 10.8a15 15 0 0 0 6.6 6.6l2.2-2.2a1 1 0 0 1 1-.25 11 11 0 0 0 3.6.6 1 1 0 0 1 1 1V20a1 1 0 0 1-1 1A17 17 0 0 1 3 4a1 1 0 0 1 1-1h3.5a1 1 0 0 1 1 1 11 11 0 0 0 .6 3.6 1 1 0 0 1-.25 1z" fill="none" stroke="#fff" stroke-width="1.8"/></svg>
  </a>
  <span class="play"><svg width="14" height="16" viewBox="0 0 14 16"><path d="M2 1l11 7-11 7z" fill="#0b4fa6"/></svg></span>
  <span class="play-label">See How We Work</span>
</header>

<section class="partners">
  <div class="partner" style="left:111px"><i></i>Northwave</div>
  <div class="partner" style="left:327px"><i></i>Tidemark</div>
  <div class="partner" style="left:540px"><i></i>Aqualine</div>
  <div class="partner" style="left:750px"><i></i>Bluecrest</div>
  <div class="partner" style="left:953px"><i></i>Shorepeak</div>
</section>

<section class="services">
  <h2 class="sec-title" style="top:793px">Services &amp; Plans<span>We Offer You</span></h2>
  <p class="sec-lead" style="top:808px">At Coral Basins, we offer bespoke pool design, renovation, and maintenance services tailored to your lifestyle. Our exclusive plans ensure seamless delivery, premium craftsmanship, and lifelong support for your investment.</p>

  <div class="card-feature">
    <div class="card-photo" role="img" aria-label="Modern villa with rectangular pool and lawn"></div>
  </div>
  <svg class="svc-icon" style="left:114px;top:996px" width="78" height="72" viewBox="0 0 78 72" fill="none" stroke="#0b4fa6" stroke-width="5">
    <line x1="0" y1="8" x2="78" y2="8"/><line x1="52" y1="0" x2="52" y2="16"/>
    <line x1="0" y1="36" x2="78" y2="36"/><line x1="20" y1="28" x2="20" y2="44"/>
    <line x1="0" y1="64" x2="78" y2="64"/><line x1="40" y1="56" x2="40" y2="72"/>
  </svg>
  <h3 class="svc-title hl" style="left:111px;top:1090px">Custom Made<br>Luxury Pools</h3>
  <p class="svc-text" style="left:111px;top:1164px">From contemporary infinity pools to classically inspired courtyards, Coral Basins delivers refined artistry and technical master craftsmanship.</p>
  <a class="btn-primary btn-service">Learn More About Service
    <svg width="22" height="22" viewBox="0 0 22 22"><circle cx="11" cy="11" r="10" fill="#fff"/><path d="M7 11h8M12 8l3 3-3 3" stroke="#0b4fa6" stroke-width="2" fill="none"/></svg>
  </a>

  <svg class="svc-icon" style="left:517px;top:990px" width="78" height="80" viewBox="0 0 78 80" fill="none" stroke="#0b4fa6" stroke-width="5">
    <path d="M6 6l60 66"/><path d="M60 66l10 8 6-6-8-10z"/>
    <path d="M40 14l14-10 18 18-10 14"/><path d="M52 26L10 70l6 6 44-42"/>
  </svg>
  <h3 class="svc-title" style="left:515px;top:1090px">Pool Renovation<br>&amp; Modernization</h3>
  <p class="svc-text" style="left:515px;top:1164px">Reimagine your existing pool with our modern renovation services. We upgrade design, technology, and materials to bring classic pools into the modern age.</p>
  <a class="btn-outline" style="left:515px;top:1292px">Learn More</a>

  <svg class="svc-icon" style="left:857px;top:1004px" width="98" height="50" viewBox="0 0 98 50" fill="none" stroke="#0b4fa6" stroke-width="5">
    <path d="M2 28l18 18L56 6"/><line x1="60" y1="4" x2="96" y2="4"/><line x1="52" y1="22" x2="86" y2="22"/><line x1="42" y1="40" x2="72" y2="40"/>
  </svg>
  <h3 class="svc-title" style="left:857px;top:1090px">Maintenance<br>&amp; Aftercare</h3>
  <p class="svc-text" style="left:857px;top:1164px">Our dedicated maintenance service ensures that your pool remains as stunning as the day it was completed.</p>
  <a class="btn-outline" style="left:857px;top:1292px">Learn More</a>

  <div class="slider">
    <svg class="abs" style="left:44px;top:12px" width="30" height="16" viewBox="0 0 30 16"><path d="M28 8H4M10 2L3 8l7 6" stroke="#b8bcc4" stroke-width="3" fill="none"/></svg>
  </div>
  <div class="slider-next"><svg width="30" height="18" viewBox="0 0 30 18"><path d="M2 9h22" stroke="#0b4fa6" stroke-width="3"/><path d="M18 2l10 7-10 7z" fill="#0b4fa6"/></svg></div>
</section>

<section class="about" role="img" aria-label="Deep blue rippled water backdrop"></section>
<div class="about-back"></div>
<div class="about-photo" role="img" aria-label="Overwater villa at dusk with illuminated blue plunge pool"></div>
<h2 class="about-title">About<br>Coral Basins</h2>
<p class="about-text">At Coral Basins, we believe that a pool is more than a feature – it's a lifestyle statement. Our collections embody precision engineering, distinctive design, and enduring quality.</p>
<ul class="about-list">
  <li>Custom-built pools from the finest materials</li>
  <li>Seamless integration with architectural styles</li>
  <li>Advanced technology for durability and efficiency</li>
  <li>Personal project guidance from design to installation</li>
</ul>
<a class="btn-white">Learn More
  <svg width="18" height="18" viewBox="0 0 18 18"><circle cx="9" cy="9" r="7.5" fill="none" stroke="#0b4fa6" stroke-width="1.5"/><line x1="9" y1="8" x2="9" y2="13" stroke="#0b4fa6" stroke-width="1.6"/><circle cx="9" cy="5.5" r="1" fill="#0b4fa6"/></svg>
</a>

<section class="reviews">
  <h2 class="sec-title" style="top:2303px">Hear What<span>People Talk of Us</span></h2>
  <p class="sec-lead" style="top:2318px">Our clients are at the heart of everything we create.<br>Read inspiring stories and genuine experiences from those who turned their dream pools into reality with Coral Basins.</p>

  <article class="review" style="left:114px">
    <span class="quote">“</span>
    <div class="stars"><svg width="132" height="24" viewBox="0 0 132 24"><g fill="#0b4fa6"><path id="st" d="M12 1l3.2 7 7.6.7-5.8 5 1.8 7.4L12 17.2 5.2 21.1 7 13.7 1.2 8.7l7.6-.7z"/><use href="#st" x="27"/><use href="#st" x="54"/><use href="#st" x="81"/><use href="#st" x="108"/></g></svg></div>
    <div class="avatar">D</div><div class="rev-name">Daniel Hart M.</div>
    <p class="rev-text">'Coral Basins transformed our backyard into a true retreat. The design exceeded our expectations and reflects pure sophistication. Every detail shows their passion for perfection.'</p>
  </article>
  <article class="review" style="left:426px">
    <span class="quote">“</span>
    <div class="stars"><svg width="132" height="24" viewBox="0 0 132 24"><g fill="#0b4fa6"><use href="#st"/><use href="#st" x="27"/><use href="#st" x="54"/><use href="#st" x="81"/><use href="#st" x="108"/></g></svg></div>
    <div class="avatar">E</div><div class="rev-name">Elena Brooks S.</div>
    <p class="rev-text">'Our infinity pool is a masterpiece. The team handled everything with professionalism and creativity, delivering on time and beyond imagination. A seamless luxury experience.'</p>
  </article>
  <article class="review" style="left:737px">
    <span class="quote">“</span>
    <div class="stars"><svg width="132" height="24" viewBox="0 0 132 24"><g fill="#0b4fa6"><use href="#st"/><use href="#st" x="27"/><use href="#st" x="54"/><use href="#st" x="81"/><use href="#st" x="108"/></g></svg></div>
    <div class="avatar">S</div><div class="rev-name">Samuel Reed R.</div>
    <p class="rev-text">'The craftsmanship and attention to detail are unmatched. From design to installation, Coral Basins made the entire process effortless and enjoyable.'</p>
  </article>
  <article class="review" style="left:1049px">
    <span class="quote">“</span>
    <div class="stars"><svg width="132" height="24" viewBox="0 0 132 24"><g fill="#0b4fa6"><use href="#st"/><use href="#st" x="27"/><use href="#st" x="54"/><use href="#st" x="81"/><use href="#st" x="108"/></g></svg></div>
    <div class="avatar">D</div><div class="rev-name">Dara Whitfield</div>
    <p class="rev-text">'We wanted something timeless – they delivered exactly that. The quality, finish and service were truly exceptional.'</p>
  </article>
</section>

<footer class="footer">
  <div class="foot-brand"><i></i>Coral Basins</div>
  <nav class="foot-nav"><a>Home</a><a>Services</a><a>About Us</a><a>Testimonials</a><a>Contact</a></nav>
  <div class="socials"><i></i><i></i><i></i><i></i></div>
  <p class="copy">© 2025 Coral Basins. All Rights Reserved.</p>
</footer>

</body>
</html>
```